A private security company called "Tavron Security Services Ltd"

Hello everybody,

We need a web page for a company based in NZ. It is mainly an informative website so it would be wonderful if the designer puts their absolute best into making it a website that I would really appreciate. The website needs to show professionalism and also needs to make our web surfers find the information they need in a click. the company's colour is black and silver, and if those two colours could be integrated into the website it would be absolutely lovely. Please do contact me for any information.

Sincerely,
Dorian Vaskel

Industry/Entity Type

Security

```html
<!DOCTYPE html>
<html lang="en">
<head>
<meta charset="utf-8">
<title>Tavron Security Services Ltd</title>
<link href="https://fonts.googleapis.com/css2?family=Crimson+Text:wght@400;600&family=Raleway:wght@500&family=Noto+Sans:wght@400;500&display=swap" rel="stylesheet">
<style>
  :root{
    --black:#1e1e1e;
    --ink:#111111;
    --text:#2b2b2b;
    --silver-light:#ffffff;
    --silver-mid:#e2e2e2;
    --silver-band:#ebebeb;
    --frame:#6e6e6e;
    --rule:#9a9a9a;
    --footer:#2a2a2a;
    --footer-text:#b8b8b8;
    --card-border:#a8a8a8;
  }
  *{margin:0;padding:0;box-sizing:border-box}
  html,body{width:1151px;height:1200px;overflow:hidden;background:#fff}
  .page{position:relative;width:1151px;height:1200px;overflow:hidden;font-family:Arial,Helvetica,sans-serif;color:var(--text)}

  .topbar{position:absolute;left:0;top:0;width:100%;height:84px;background:#fff}
  .call{position:absolute;left:804px;top:26px;display:flex;align-items:center;gap:10px}
  .call-label{font-family:"Noto Sans",sans-serif;font-size:15px;color:#333;line-height:16px}
  .call-number{font-family:Arial,Helvetica,sans-serif;font-size:24px;color:#555;letter-spacing:-0.5px;line-height:26px}

  .navband{position:absolute;left:0;top:84px;width:100%;height:47px;
    background:linear-gradient(#f4f4f4,#ffffff 40%,#e6e6e6);box-shadow:0 2px 3px rgba(0,0,0,.15)}
  .brand{position:absolute;left:118px;top:-2px;width:170px;text-align:center;font-family:"Crimson Text",serif;font-weight:600;color:var(--ink);line-height:1}
  .brand-name{font-size:25px;letter-spacing:1.5px;text-transform:uppercase}
  .brand-sub{font-size:11px;letter-spacing:.3px}
  .nav{position:absolute;top:0;height:47px;display:flex;left:448px}
  .nav a{font-family:Raleway,sans-serif;font-weight:500;font-size:15px;color:#111;text-decoration:none;letter-spacing:.6px;display:flex;align-items:center;justify-content:center;height:47px;border-right:1px solid #c8c8c8}
  .nav a:last-child{border-right:none}

  .darkband{position:absolute;left:0;top:131px;width:100%;height:257px;background:var(--black)}
  .hero{position:absolute;left:95px;top:160px;width:959px;height:343px;border:5px solid var(--frame);background:#fff}
  .hero-photo{position:absolute;inset:0;background:linear-gradient(180deg,#9a9a9a 0%,#5c5c5c 45%,#3a3a3a 70%,#8a8a8a 100%)}
  .hero-caption{position:absolute;left:183px;top:154px;width:551px;height:58px;background:rgba(0,0,0,.55);
    font-family:"Crimson Text",serif;color:#fff;font-size:37px;line-height:58px;text-align:center}
  .hero-shadow{position:absolute;left:140px;top:503px;width:870px;height:20px;background:radial-gradient(ellipse at top,rgba(0,0,0,.28),rgba(0,0,0,0) 70%)}

  .welcome{position:absolute;left:0;top:538px;width:100%;text-align:center;font-family:"Crimson Text",serif;font-size:31px;letter-spacing:2px;color:var(--ink)}
  .intro{position:absolute;left:100px;top:603px;width:951px;text-align:center;font-size:13px;line-height:19px;color:#2b2b2b}
  .intro p+p{margin-top:19px}

  .services{position:absolute;left:0;top:772px;width:100%;height:336px;background:var(--silver-band)}
  .services-title{position:absolute;left:0;top:18px;width:100%;text-align:center;font-family:"Crimson Text",serif;font-size:38px;color:var(--ink)}
  .rule{position:absolute;top:38px;height:12px}
  .card{position:absolute;top:123px;width:210px;height:145px;background:#fff;border:1px solid var(--card-border);text-align:center}
  .card-badge{position:absolute;left:50%;top:-36px;width:79px;height:79px;margin-left:-40px;border-radius:50%;background:var(--ink)}
  .card-title{position:absolute;left:0;top:55px;width:100%;font-family:"Noto Sans",sans-serif;font-weight:500;font-size:21px;line-height:28px;color:#1a1a1a}
  .card-more{position:absolute;left:0;top:127px;width:100%;font-family:"Noto Sans",sans-serif;font-size:11.5px;color:#333}
  .chev{display:inline-block;vertical-align:middle;margin-left:2px}
  .more-link{position:absolute;right:105px;top:300px;font-family:"Noto Sans",sans-serif;font-size:11.5px;color:#222}

  .footer{position:absolute;left:0;top:1108px;width:100%;height:92px;background:var(--footer)}
  .footer-nav{position:absolute;left:105px;top:22px;font-size:12.5px;color:var(--footer-text);letter-spacing:.3px}
  .footer-nav span.sep{margin:0 14px}
  .copyright{position:absolute;left:105px;top:54px;font-size:12px;color:var(--footer-text);letter-spacing:.3px}
  .footer-brand{position:absolute;left:935px;top:42px;width:130px;text-align:center;font-family:"Crimson Text",serif;font-weight:600;color:#e4e4e4;line-height:1}
  .footer-brand .brand-name{font-size:19px;letter-spacing:1px}
  .footer-brand .brand-sub{font-size:9px}
</style>
</head>
<body>
<div class="page">
  <header class="topbar">
    <div class="call">
      <svg width="30" height="30" viewBox="0 0 24 24" aria-hidden="true"><path fill="#666" d="M6.6 10.8c1.4 2.8 3.8 5.1 6.6 6.6l2.2-2.2c.3-.3.7-.4 1-.2 1.1.4 2.3.6 3.6.6.6 0 1 .4 1 1V20c0 .6-.4 1-1 1C10.6 21 3 13.4 3 4c0-.6.4-1 1-1h3.5c.6 0 1 .4 1 1 0 1.3.2 2.5.6 3.6.1.3 0 .7-.2 1z"/></svg>
      <div>
        <div class="call-label">Call Now Today</div>
        <div class="call-number">+7 (495) 310-42-58</div>
      </div>
    </div>
  </header>

  <nav class="navband">
    <div class="brand"><div class="brand-name">Tavron</div><div class="brand-sub">Security Services Ltd.</div></div>
    <div class="nav">
      <a href="#" style="width:98px">HOME</a>
      <a href="#" style="width:119px">ABOUT</a>
      <a href="#" style="width:135px">SERVICES</a>
      <a href="#" style="width:108px">BLOG</a>
      <a href="#" style="width:162px">CONTACT US</a>
    </div>
  </nav>

  <div class="darkband"></div>
  <section class="hero">
    <div class="hero-photo" role="img" aria-label="Black and white photo of two uniformed security guards standing at a glass building entrance"></div>
    <div class="hero-caption">Personal bodyguard for high net</div>
  </section>
  <div class="hero-shadow"></div>

  <h1 class="welcome">Welcome to Tavron Security Services Ltd.</h1>
  <div class="intro">
    <p>Lorem ipsum dolor sit amet, consectetur adipiscing elit. Quisque dapibus accumsan orci, pretium eleifend arcu adipiscing eget. Fusce accumsan facilisis tincidunt. Phasellus tempor enim purus, vitae venenatis est. Ut imperdiet hendrerit pulvinar. Cras at tellus a enim dapibus accumsan orci, pretium eleifend arcu adipiscing eget. Fusce accumsan facilisis tincidunt. Phasellus tempor enim purus, vitae venenatis est. Ut imperdiet hendrerit pulvinar.</p>
    <p>Mauris dolor magna, elementum eu dictum eu, fermentum a nibh. Praesent ut dui lectus, vel lacinia sem. Praesent commodo malesuada urna, quis convallis risus dictum et. Nunc dapibus interdum libero, et semper eros auctor ac.</p>
  </div>

  <section class="services">
    <svg class="rule" style="left:100px" width="243" height="12" aria-hidden="true"><line x1="0" y1="6" x2="228" y2="6" stroke="var(--rule)" stroke-width="1"/><polygon points="230,0 242,6 230,12" fill="#8a8a8a"/></svg>
    <svg class="rule" style="left:804px" width="243" height="12" aria-hidden="true"><polygon points="13,0 1,6 13,12" fill="#8a8a8a"/><line x1="15" y1="6" x2="243" y2="6" stroke="var(--rule)" stroke-width="1"/></svg>
    <h2 class="services-title">The services i provide are:</h2>

    <article class="card" style="left:91px"><div class="card-badge"></div><div class="card-title">Property<br>Guards</div><div class="card-more">More Details <svg class="chev" width="9" height="8" viewBox="0 0 9 8"><path d="M1 1l3 3-3 3M5 1l3 3-3 3" stroke="#555" stroke-width="1.4" fill="none"/></svg></div></article>
    <article class="card" style="left:344px"><div class="card-badge"></div><div class="card-title">Corporate events<br>security</div><div class="card-more">More Details <svg class="chev" width="9" height="8" viewBox="0 0 9 8"><path d="M1 1l3 3-3 3M5 1l3 3-3 3" stroke="#555" stroke-width="1.4" fill="none"/></svg></div></article>
    <article class="card" style="left:593px"><div class="card-badge"></div><div class="card-title">Security<br>Consultancy</div><div class="card-more">More Details <svg class="chev" width="9" height="8" viewBox="0 0 9 8"><path d="M1 1l3 3-3 3M5 1l3 3-3 3" stroke="#555" stroke-width="1.4" fill="none"/></svg></div></article>
    <article class="card" style="left:840px"><div class="card-badge"></div><div class="card-title">Private<br>Investigation</div><div class="card-more">More Details <svg class="chev" width="9" height="8" viewBox="0 0 9 8"><path d="M1 1l3 3-3 3M5 1l3 3-3 3" stroke="#555" stroke-width="1.4" fill="none"/></svg></div></article>

    <div class="more-link">More Than <svg class="chev" width="9" height="8" viewBox="0 0 9 8"><path d="M1 1l3 3-3 3M5 1l3 3-3 3" stroke="#555" stroke-width="1.4" fill="none"/></svg></div>
  </section>

  <footer class="footer">
    <div class="footer-nav">HOME<span class="sep">|</span>ABOUT<span class="sep">|</span>SERVICES<span class="sep">|</span>BLOG<span class="sep">|</span>CONTACT US</div>
    <div class="copyright">© 2014 . All right reserved. Privacy Policy | Terms &amp; Conditions</div>
    <div class="footer-brand"><div class="brand-name">TAVRON</div><div class="brand-sub">Security Services Ltd.</div></div>
  </footer>
</div>
</body>
</html>
```